Tarvolen - Tarvolen Border Flow Reshaping Trade

Web Design for international start-up, which is automating customs clearance processes for forwarding companies by applying a web application, which is operating with artificial intelligence and robotic process automation. Tarvolen pursues the vision of supporting forwarding companies successfully in becoming digital masters and co-creates innovative software solutions with all participants (ex- and importers of goods) along value-added chains. With intelligent/smart/digital customs clearance software or in other words, a virtual customs clearance roboter tailord to the customers needs, we are transforming businesses. The website could look like this:

https://www.plomix.com/uk-en/index.php
or
https://sitebrenna.com/theme/halvering

Please use colours and designs you think would be the best fit. These websites are just here to give you an idea of how the webdesign could look like. Use the attached logo design as a basis for further web design. You can use the provided pictures, but you can also use your own ones, if you think they are better suited. But please take care, that they have a high resolution quality.

Description of Website: The website is transparent and modern. It provides seven pages such as homepage, products, web app, the about us, working at Tarvolen, News, contact us and search results page. The homepage or landing page should be filled with a short description of the company, what Tarvolen is doing, how they will support its customers and will also include a video of the provided solution. Products provide obviously information about different products and their characteristics. Web app page includes information about principles and technologies that get the software going. The about us page includes unique advantages and value propositions for customers and the contact us, as the name already says, will provide contact information and possibilities to contact us. The rest is also obvious (for additional information look up the website of PLX, priorly provided link - the page is also available in english).

If you have any questions, I am happy to answer them any time.
Updates

I have to think about the text that I want to have included into the design and hadn't have the time to compose it.

Target Market(s)

Forwarding Companies, Ex-/Importers

Industry/Entity Type

It Company

Number of Pages Required

5+ page

Requirements
Must have
• The web design should be designes according to the attached logo of Tarvolen.

```html
<!DOCTYPE html>
<html lang="en">
<head>
<meta charset="utf-8">
<title>Tarvolen – Border Flow Power</title>
<link rel="stylesheet" href="https://fonts.googleapis.com/css2?family=Roboto:wght@400;500;700&family=Open+Sans:wght@400;600;700&display=swap">
<style>
:root{
  --indigo:#3e4ba6;
  --indigo-deep:#2f3a8f;
  --cyan:#1fb6d6;
  --ink:#222;
  --text:#777;
  --line:#cfd3de;
  --white:#fff;
}
*{box-sizing:border-box;margin:0;padding:0}
html,body{width:1200px;height:3639px;overflow:hidden}
body{position:relative;background:var(--white);font-family:"Open Sans",sans-serif;color:var(--text)}
.abs{position:absolute}
.center{left:0;width:1200px;text-align:center}

/* header */
.site-header{top:0;left:0;width:1200px;height:98px;background:var(--white);border-bottom:1px solid #e6e6e6}
.brand{left:112px;top:22px;display:flex;align-items:center;gap:10px}
.brand-mark{width:30px;height:30px;border:4px solid var(--cyan);border-radius:50%}
.brand-name{font-family:"Roboto",sans-serif;font-weight:700;font-size:38px;color:var(--indigo);line-height:1}
.brand-tag{position:absolute;left:100px;top:42px;font-size:11px;color:var(--indigo);white-space:nowrap}
.main-nav{top:41px;left:434px;display:flex;gap:21px;font-family:"Roboto",sans-serif;font-size:15.5px;font-weight:500;color:#222}
.main-nav .active{color:var(--cyan)}
.search-icon{left:1074px;top:42px}

/* hero */
.hero{top:98px;left:0;width:1200px;height:582px;background:radial-gradient(ellipse at 55% 110%,#6a5a3a 0%,#2b3242 35%,#0b0f1a 70%,#020306 100%)}
.hero-title{top:292px;font-family:"Roboto",sans-serif;font-weight:700;font-size:63px;color:var(--white)}
.btn{display:inline-flex;align-items:center;justify-content:center;border-radius:30px;font-family:"Open Sans",sans-serif;font-weight:700;text-transform:uppercase}
.btn-light{left:509px;top:403px;width:184px;height:58px;background:var(--white);color:#222;font-size:18px}
.slider-dots{top:592px;left:563px;display:flex;gap:5px}
.slider-dots span{width:14px;height:14px;border:2px solid var(--white);border-radius:50%}
.slider-dots span.on{background:var(--white)}

/* welcome */
.welcome{top:680px;left:0;width:1200px;height:627px;background:linear-gradient(90deg,#c8ccd3 0%,#eef0f3 20%,#f4f5f7 50%,#eef0f3 80%,#c4c9d1 100%)}
.eyebrow{font-family:"Roboto",sans-serif;font-weight:500;font-size:33px;color:var(--indigo);text-transform:uppercase}
.heading{font-family:"Roboto",sans-serif;font-weight:700;font-size:51px;color:var(--ink);text-transform:uppercase}
.welcome-eyebrow{top:808px}
.welcome-heading{top:866px}
.welcome-copy{top:966px;left:283px;width:634px;text-align:center;font-size:14.6px;line-height:32.5px}
.btn-cyan{background:var(--cyan);color:var(--white);font-size:16px}
.about-btn{left:521px;top:1170px;width:159px;height:58px}

/* services */
.services-eyebrow{top:1412px;left:112px}
.services-heading{top:1470px;left:112px}
.services-copy{top:1558px;left:112px;width:430px;font-size:14.6px;line-height:30px}
.read-btn{left:112px;top:1714px;width:158px;height:58px}
.service-icon{width:122px;height:122px;border:1.5px solid #9aa0b8;border-radius:50%;background:var(--white);display:flex;align-items:center;justify-content:center}
.service-title{font-family:"Roboto",sans-serif;font-size:25px;line-height:35px;color:var(--ink)}
.service-text{font-size:14.6px;line-height:28px;width:270px}

/* process */
.process{top:1881px;left:0;width:1200px;height:724px;background:linear-gradient(180deg,rgba(62,75,166,.96),rgba(70,82,175,.92) 50%,rgba(62,75,166,.97)),linear-gradient(90deg,#5a6698,#7d8cad)}
.process-eyebrow{top:1968px;color:var(--white)}
.process-heading{top:2026px;color:var(--white)}
.step-halo{width:154px;height:154px;border-radius:50%;background:rgba(255,255,255,.22);display:flex;align-items:center;justify-content:center}
.step-disc{width:136px;height:136px;border-radius:50%;background:var(--white);display:flex;align-items:center;justify-content:center}
.step-label{width:260px;text-align:center;font-family:"Roboto",sans-serif;font-size:21px;line-height:34px;color:var(--white)}
.connector{height:3px;background:var(--cyan);top:2204px}

/* video */
.video{left:290px;top:2471px;width:620px;height:396px;background:linear-gradient(135deg,#7d8a93 0%,#4d5a66 35%,#2a3a63 70%,#5f6a78 100%)}
.play{left:564px;top:2633px;width:72px;height:72px;border-radius:50%;background:#111;display:flex;align-items:center;justify-content:center}

/* contact */
.contact-eyebrow{top:2971px}
.contact-heading{top:3032px}
.sub-heading{font-family:"Roboto",sans-serif;font-size:22px;color:var(--ink);font-weight:500}
.field{border:1px solid #b9bdc8;border-radius:5px;background:var(--white);font-size:13.5px;color:#777;padding:14px 15px;line-height:1}
.submit{left:618px;top:3446px;width:96px;height:40px;font-size:14px}
.info-row{left:779px;display:flex;align-items:center;gap:14px;font-size:13.5px;line-height:24px;color:#555}
.info-icon{width:34px;height:34px;border:1px solid #c9ccd6;border-radius:50%;display:flex;align-items:center;justify-content:center;flex:none}
.social{top:3463px;left:775px;display:flex;gap:10px}
.social span{width:36px;height:36px;border:1px solid #c9ccd6;border-radius:50%;display:flex;align-items:center;justify-content:center}
.social span i{width:12px;height:12px;border-radius:50%;background:var(--indigo)}
.footer-rule{left:112px;top:3541px;width:968px;height:1px;background:#ccc}
.copyright{top:3581px;font-size:13.5px;color:#555}
.to-top{left:1062px;top:3578px}
</style>
</head>
<body>

<header class="abs site-header">
  <div class="abs brand">
    <span class="brand-mark"></span>
    <span class="brand-name">Tarvolen</span>
    <span class="brand-tag">Border Flow Power</span>
  </div>
  <nav class="abs main-nav">
    <span class="active">Home</span><span>Products</span><span>Web app</span><span>About us</span><span>working at Tarvolen</span><span>News</span><span>Contact us</span>
  </nav>
  <svg class="abs search-icon" width="16" height="16" viewBox="0 0 16 16"><circle cx="6.5" cy="6.5" r="5" fill="none" stroke="#222" stroke-width="2.2"/><line x1="10" y1="10" x2="15" y2="15" stroke="#222" stroke-width="2.6" stroke-linecap="round"/></svg>
</header>

<section class="abs hero" role="img" aria-label="Night view of Earth from orbit with glowing city lights"></section>
<h1 class="abs center hero-title">Border Flow Power</h1>
<span class="abs btn btn-light">Get started</span>
<div class="abs slider-dots"><span class="on"></span><span></span><span></span><span></span></div>

<section class="abs welcome" role="img" aria-label="Upward view of glass skyscrapers against a pale sky"></section>
<p class="abs center eyebrow welcome-eyebrow">Welcome</p>
<h2 class="abs center heading welcome-heading">Tarvolen</h2>
<p class="abs welcome-copy">Nam libero tempore, cum soluta nobis est eligendi optio cumque nihil impedit quo minu id quod maxime placeat facere possimus, omnis voluptas assumenda est, omnis dolor repell endu oribus autem quibusdam et aut officiis debitis aut rerum necessitatibus saepe eveniet ut et voluptates repudiandae sint et molestiae non recusan aque earum rerum hic tene tur a sapiente delectus, ut aut reiciendi ptatibus maiores alias.</p>
<span class="abs btn btn-cyan about-btn">About us</span>

<p class="abs eyebrow services-eyebrow">Services</p>
<h2 class="abs heading services-heading">What Tarvolen is</h2>
<p class="abs services-copy">We are an international start-up, which is automating customs clearance processes for forwarding companies by applying a web application, which is operating with artificial intelligence and robotic process automation.</p>
<span class="abs btn btn-cyan read-btn">Read more</span>

<div class="abs service-icon" style="left:671px;top:1434px">
  <svg width="70" height="70" viewBox="0 0 70 70" fill="none" stroke="#3e4ba6" stroke-width="2"><path d="M35 8c-8 0-12 5-12 9-7 1-11 7-9 13-5 4-4 13 2 15 0 7 6 11 12 9 2 5 5 7 7 7s5-2 7-7c6 2 12-2 12-9 6-2 7-11 2-15 2-6-2-12-9-13 0-4-4-9-12-9z"/><line x1="35" y1="10" x2="35" y2="60"/><circle cx="25" cy="25" r="2.5" stroke="#1fb6d6"/><circle cx="45" cy="30" r="2.5" stroke="#1fb6d6"/><circle cx="26" cy="42" r="2.5" stroke="#1fb6d6"/><circle cx="44" cy="47" r="2.5" stroke="#1fb6d6"/><path d="M27 25h8M35 30h8M28 42h7M35 47h7"/></svg>
</div>
<h3 class="abs service-title" style="left:827px;top:1430px">Artificial<br>Intelligence</h3>
<p class="abs service-text" style="left:827px;top:1508px">Nam libero tempore, cum soluta nobis est eligendi optio cumque.</p>

<div class="abs service-icon" style="left:671px;top:1614px">
  <svg width="70" height="70" viewBox="0 0 70 70" fill="none" stroke="#3e4ba6" stroke-width="2"><path d="M16 40c-4 0-6 4-4 7 2 4 7 4 9 2 2 5 9 6 13 3 4 3 11 2 13-3 2 2 7 2 9-2 2-3 0-7-4-7"/><circle cx="35" cy="47" r="7" stroke="#1fb6d6"/><circle cx="35" cy="47" r="3" stroke="#1fb6d6"/><path d="M20 36V24M28 36V18M35 36V14M42 36V18M50 36V24"/><circle cx="20" cy="21" r="2.5"/><circle cx="28" cy="15" r="2.5"/><circle cx="35" cy="11" r="2.5"/><circle cx="42" cy="15" r="2.5"/><circle cx="50" cy="21" r="2.5"/></svg>
</div>
<h3 class="abs service-title" style="left:827px;top:1610px">Robotic Process<br>Automation</h3>
<p class="abs service-text" style="left:827px;top:1688px">Nam libero tempore, cum soluta nobis est eligendi optio cumque.</p>

<section class="abs process" role="img" aria-label="Aerial view of a container port with cranes under an indigo overlay"></section>
<p class="abs center eyebrow process-eyebrow">Process</p>
<h2 class="abs center heading process-heading">How it works</h2>

<div class="abs connector" style="left:292px;width:103px"></div>
<div class="abs connector" style="left:549px;width:106px"></div>
<div class="abs connector" style="left:809px;width:106px"></div>
<svg class="abs" style="left:337px;top:2194px" width="16" height="24" viewBox="0 0 16 24"><polyline points="3,2 13,12 3,22" fill="none" stroke="#fff" stroke-width="3"/></svg>
<svg class="abs" style="left:595px;top:2194px" width="16" height="24" viewBox="0 0 16 24"><polyline points="3,2 13,12 3,22" fill="none" stroke="#fff" stroke-width="3"/></svg>
<svg class="abs" style="left:855px;top:2194px" width="16" height="24" viewBox="0 0 16 24"><polyline points="3,2 13,12 3,22" fill="none" stroke="#fff" stroke-width="3"/></svg>

<div class="abs step-halo" style="left:138px;top:2128px"><div class="step-disc">
  <svg width="58" height="52" viewBox="0 0 58 52"><rect x="2" y="2" width="54" height="36" rx="3" fill="#1fb6d6"/><rect x="7" y="7" width="44" height="26" fill="#fff"/><rect x="24" y="38" width="10" height="8" fill="#1fb6d6"/><rect x="16" y="46" width="26" height="4" fill="#1fb6d6"/></svg>
</div></div>
<div class="abs step-halo" style="left:395px;top:2128px"><div class="step-disc">
  <svg width="44" height="56" viewBox="0 0 44 56"><path d="M2 2h28l12 12v40H2z" fill="#1fb6d6"/><path d="M30 2v12h12" fill="#8fdcec"/><rect x="10" y="26" width="24" height="3" fill="#fff"/><rect x="10" y="33" width="24" height="3" fill="#fff"/><rect x="10" y="40" width="24" height="3" fill="#fff"/></svg>
</div></div>
<div class="abs step-halo" style="left:655px;top:2128px"><div class="step-disc">
  <svg width="56" height="52" viewBox="0 0 56 52" fill="none" stroke="#1fb6d6" stroke-width="4"><path d="M30 10H6v38h38V26"/><path d="M46 4l6 6-22 22-9 3 3-9z" fill="#1fb6d6"/></svg>
</div></div>
<div class="abs step-halo" style="left:915px;top:2128px"><div class="step-disc">
  <svg width="56" height="52" viewBox="0 0 56 52" fill="none" stroke="#1fb6d6" stroke-width="4"><path d="M30 10H6v38h38V26"/><path d="M46 4l6 6-22 22-9 3 3-9z" fill="#1fb6d6"/></svg>
</div></div>

<p class="abs step-label" style="left:85px;top:2307px">Apply a<br>web application</p>
<p class="abs step-label" style="left:342px;top:2307px">Present your waybill to<br>custom supervisor</p>
<p class="abs step-label" style="left:602px;top:2307px">Review your<br>declaration</p>
<p class="abs step-label" style="left:862px;top:2307px">Collect your<br>consignment</p>

<div class="abs video" role="img" aria-label="Video still of an employee working at a desk with monitors"></div>
<div class="abs play"><svg width="26" height="30" viewBox="0 0 26 30"><polygon points="4,2 24,15 4,28" fill="#fff"/></svg></div>

<p class="abs center eyebrow contact-eyebrow">Contact</p>
<h2 class="abs center heading contact-heading">Get in touch</h2>

<h3 class="abs sub-heading" style="left:110px;top:3160px">Contact form</h3>
<div class="abs field" style="left:112px;top:3218px;width:296px;height:46px">Name :</div>
<div class="abs field" style="left:417px;top:3218px;width:297px;height:46px">Phone no :</div>
<div class="abs field" style="left:112px;top:3280px;width:602px;height:46px">Email :</div>
<div class="abs field" style="left:112px;top:3341px;width:602px;height:84px">Message :</div>
<span class="abs btn btn-cyan submit">Submit</span>

<h3 class="abs sub-heading" style="left:778px;top:3160px">Contact Information</h3>
<div class="abs info-row" style="top:3212px">
  <span class="info-icon"><svg width="14" height="18" viewBox="0 0 14 18"><path d="M7 1a6 6 0 0 0-6 6c0 5 6 10 6 10s6-5 6-10a6 6 0 0 0-6-6z" fill="none" stroke="#1fb6d6" stroke-width="1.6"/><circle cx="7" cy="7" r="2" fill="#1fb6d6"/></svg></span>
  <span>47 Harlow Quay Suite 9<br>Brennick Bay, FL 30219</span>
</div>
<div class="abs info-row" style="top:3280px">
  <span class="info-icon"><svg width="14" height="14" viewBox="0 0 14 14"><path d="M3 1l3 3-2 2c1 2 2 3 4 4l2-2 3 3-2 2C6 13 1 8 1 3z" fill="#1fb6d6"/></svg></span>
  <span>1 555 014 2270</span>
</div>
<div class="abs info-row" style="top:3340px">
  <span class="info-icon"><svg width="15" height="11" viewBox="0 0 15 11"><rect x="0.5" y="0.5" width="14" height="10" rx="1" fill="#1fb6d6"/><polyline points="1,1 7.5,6 14,1" fill="none" stroke="#fff" stroke-width="1.3"/></svg></span>
  <span>info@tarvolen.com</span>
</div>

<h3 class="abs sub-heading" style="left:778px;top:3418px">Social Media</h3>
<div class="abs social"><span><i></i></span><span><i></i></span><span><i></i></span></div>

<div class="abs footer-rule"></div>
<p class="abs center copyright">Copyright © 2019, Tarvolen. All rights reserved.</p>
<svg class="abs to-top" width="30" height="18" viewBox="0 0 30 18"><polyline points="2,16 15,3 28,16" fill="none" stroke="#bbb" stroke-width="2.5"/></svg>

</body>
</html>
```